Vernac Law Business cards and stationary design project

We are looking for a stationary design for business cards (double sided), 8x10, 5x7, and legal and standard envelopes.

We would like the design to match the logo that we have already.
Color palate preferred is Teal, White, grey and any others that will look good for a professional law firm.

We would like this statement: "RELATIONSHIPS. RESPECT. RESULT" to be on the back of the business cards and maybe on the stationary if it looks good.

Please see link to website for more information: www.vernac-law.example

Target Market(s)

Potential clients that need Attorney services.

Industry/Entity Type

Law Firm

Contact Information for Business Card

We would like the front and back to be two different colors. Current business cards are teal front, grey back and are a vertical design. We are open to options with colors.

Font styles to use
Serif

Colors
33a6d7
33b8a4
b9b9b9
5c5c5c

Requirements
Must have
• Logo supplied needs to go on the card and stationary.
• Match website color palate, www.vernac-law.example
• Be professional and not too wordy.
• Criminal Law, Civil Litigation, Personal Injury, Restraining Orders need to be on the card.
Nice to have
• RELATIONSHIPS. RESPECT. RESULTS. on the back of the card.
Should not have
• Not be too busy/wordy or too flashy.

```html
<!DOCTYPE html>
<html lang="en">
<head>
<meta charset="utf-8">
<title>Vernac Law – Business Card</title>
<link rel="stylesheet" href="https://fonts.googleapis.com/css2?family=Cinzel:wght@400;600;700&family=Tinos&display=swap">
<style>
  :root {
    --teal: #12889a;
    --teal-text: #1a8796;
    --ink: #4a4a4a;
    --paper: #ffffff;
    --backdrop: #e9e9e9;
  }
  * { box-sizing: border-box; margin: 0; padding: 0; }
  html, body {
    width: 1105px; height: 1200px; overflow: hidden;
    background: var(--backdrop);
  }
  .canvas { position: relative; width: 1105px; height: 1200px; }
  .card {
    position: absolute; left: 196px; width: 720px; height: 410px;
    box-shadow: 0 4px 14px rgba(0,0,0,0.25);
  }
  .card-front { top: 146px; background: var(--paper); }
  .card-back { top: 602px; background: var(--teal); }

  .firm-mark {
    position: absolute; left: 100px; top: 170px; width: 230px;
    text-align: center;
    font-family: "Cinzel", serif; font-weight: 400;
    font-size: 33px; color: var(--teal-text); letter-spacing: 0.5px;
  }
  .firm-mark .dot {
    display: block; width: 18px; height: 18px; margin: 0 auto 14px;
    border-radius: 50%; background: var(--teal-text);
  }

  .contact-block { position: absolute; left: 373px; top: 102px; }
  .person-name {
    font-family: "Cinzel", serif; font-weight: 600;
    font-size: 33px; color: var(--teal-text); line-height: 1.1;
  }
  .person-title {
    font-family: "Cinzel", serif; font-size: 22px; color: var(--ink);
    margin-top: 2px; letter-spacing: 0.5px;
  }
  .contact-list { list-style: none; margin-top: 26px; }
  .contact-list li {
    display: flex; align-items: center; gap: 14px;
    font-family: "Tinos", serif; font-size: 21px; color: var(--ink);
    height: 30.5px;
  }
  .contact-list svg { width: 18px; height: 18px; fill: var(--teal-text); flex: none; }

  .tagline-band {
    position: absolute; left: 0; right: 0; top: 355px; height: 40px;
    background: var(--teal);
    display: flex; align-items: center; justify-content: center;
    font-family: "Cinzel", serif; font-weight: 700;
    font-size: 22px; color: #fff; letter-spacing: 0.5px;
  }

  .back-mark {
    position: absolute; left: 0; right: 0; top: 160px; text-align: center;
    font-family: "Cinzel", serif; font-weight: 400;
    font-size: 58px; color: #fff; letter-spacing: 1px;
  }
  .practice-areas {
    position: absolute; left: 0; right: 0; top: 350px; text-align: center;
    font-family: "Tinos", serif; font-size: 21px; color: #fff;
  }
</style>
</head>
<body>
<main class="canvas">
  <section class="card card-front">
    <div class="firm-mark"><span class="dot"></span>Vernac Law</div>
    <div class="contact-block">
      <h1 class="person-name">Dana Mercer</h1>
      <p class="person-title">Trial Lawyer</p>
      <ul class="contact-list">
        <li>
          <svg viewBox="0 0 24 24" aria-hidden="true"><path d="M6.6 10.8a15.1 15.1 0 0 0 6.6 6.6l2.2-2.2c.3-.3.7-.4 1-.2 1.1.4 2.3.6 3.6.6.6 0 1 .4 1 1V20c0 .6-.4 1-1 1A17 17 0 0 1 3 4c0-.6.4-1 1-1h3.5c.6 0 1 .4 1 1 0 1.3.2 2.5.6 3.6.1.3 0 .7-.2 1z"/></svg>
          (555) 014-2290
        </li>
        <li>
          <svg viewBox="0 0 24 24" aria-hidden="true"><path d="M2 5h20v14H2z M2 5l10 8 10-8" /><path d="M2 6.5l10 7.5 10-7.5V5H2z" fill="#fff"/></svg>
          dana@vernac-law.example
        </li>
        <li>
          <svg viewBox="0 0 24 24" aria-hidden="true"><circle cx="12" cy="12" r="10"/><path d="M8 7c2 0 3 1 3 2.5S9 11 8 12s0 3 1.5 3.5S11 18 10 20M15 5c-1 1.5 0 3 1.5 3s2 2 1 3.5" stroke="#fff" stroke-width="1.6" fill="none"/></svg>
          www.vernac-law.example
        </li>
      </ul>
    </div>
    <div class="tagline-band">RELATIONSHIPS. RESPECT. RESULTS.</div>
  </section>

  <section class="card card-back">
    <div class="back-mark">Vernac Law</div>
    <p class="practice-areas">Criminal Law, Civil Litigation/Personal Injury, Restraining</p>
  </section>
</main>
</body>
</html>
```